New Dental Office Needs an Attractive and user friendly Website Designed

I need a website for a new dental office. The Name is Harrowfield Dentistry. I would like a Modern design with a user friendly interface and usability.
I would like a landing page, a page that lists the services we offer: Cosmetic Dentistry, Implants, Dental Hygiene, Emergency Services, Restorations, Dentures
Target Market(s)
Mid to upper class
Industry/Entity Type
Dentistry
Coding
Number of Pages Required
1 page
Requirements
Must have
- Landing page that has a scheduling option, Procedures, operating hours, and contact us info
Nice to have
- Appealing design, Soft comforting colors. Easy to navigate page, Modern and professional.

```html
<!DOCTYPE html>
<html lang="en">
<head>
<meta charset="UTF-8">
<title>Harrowfield Dentistry</title>
<link href="https://fonts.googleapis.com/css2?family=Lora:wght@400;500;600&family=Inter:wght@400;500&display=swap" rel="stylesheet">
<style>
:root{
  --blue:#0a90d8;
  --blue-deep:#0678c2;
  --blue-light:#3aaeea;
  --ink:#1c1c1c;
  --text:#2b2b2b;
  --muted:#6b6b6b;
  --soft:#f6f6f6;
  --tint:#f2f8fd;
  --white:#ffffff;
  --footer:#252424;
  --field:#ffffff;
  --serif:'Lora',Georgia,serif;
  --sans:'Inter',Arial,sans-serif;
}
*{margin:0;padding:0;box-sizing:border-box}
html,body{width:1200px;height:3002px;overflow:hidden;background:var(--white)}
.page{position:relative;width:1200px;height:3002px;font-family:var(--sans);color:var(--text)}
.abs{position:absolute}

/* hero */
.hero{left:0;top:0;width:1200px;height:645px;background:linear-gradient(120deg,#1d9be0 0%,var(--blue) 45%,#0b86cf 100%)}
.brand{left:111px;top:24px;font-family:var(--serif);font-weight:500;font-size:30px;color:var(--white);line-height:1}
.brand small{display:block;font-size:16px;letter-spacing:5px;margin-top:8px;text-transform:uppercase}
.nav{left:443px;top:40px;display:flex;gap:50px;font-family:var(--serif);font-size:17px;color:var(--white)}
.btn-quote{left:955px;top:28px;width:133px;height:42px;border-radius:21px;background:var(--white);color:var(--ink);font-family:var(--serif);font-weight:500;font-size:16px;display:flex;align-items:center;justify-content:center}
.hero-title{left:0;width:1200px;top:150px;text-align:center;font-family:var(--serif);font-size:58px;color:var(--white);font-weight:400}
.hero-sub{left:0;width:1200px;top:236px;text-align:center;font-size:16px;color:var(--white);letter-spacing:-.2px}
.btn-appt{left:462px;top:285px;width:275px;height:54px;border-radius:27px;background:var(--white);color:var(--ink);font-family:var(--serif);font-weight:500;font-size:19px;display:flex;align-items:center;justify-content:center}
.hero-photo{left:163px;top:387px;width:874px;height:418px;background:linear-gradient(110deg,#cfe3f3 0%,#7fb4e6 40%,#3b8fe0 100%)}

/* about */
.about-bg{left:0;top:645px;width:1200px;height:744px;background:var(--soft)}
.about-cut{left:0;top:645px}
.photo{background:linear-gradient(160deg,#e9eef2,#b9c4cc);border-radius:6px}
.photo.room{left:111px;top:903px;width:252px;height:234px}
.photo.smile{left:111px;top:1153px;width:255px;height:236px;background:linear-gradient(160deg,#f3ece6,#d9c3a8)}
.photo.consult{left:379px;top:928px;width:253px;height:441px;background:linear-gradient(170deg,#eef1f3,#a9c9c6)}
.h2{font-family:var(--serif);font-weight:400;font-size:44px;color:var(--ink);line-height:1}
.h2 b{font-weight:600;color:var(--blue)}
.about-title{left:718px;top:898px;width:400px;line-height:44px}
.about-copy{left:720px;top:994px;width:368px;font-size:15px;line-height:25.7px;color:var(--text);text-align:justify}
.about-copy p+p{margin-top:25.7px}
.btn-blue{background:var(--blue);color:var(--white);font-family:var(--serif);font-weight:600;display:flex;align-items:center;justify-content:center;border-radius:28px}
.btn-read{left:720px;top:1294px;width:155px;height:54px;font-size:20px}

/* services */
.services-bg{left:0;top:1389px;width:1200px;height:557px;background:linear-gradient(180deg,var(--white) 0%,var(--tint) 100%)}
.services-title{left:0;width:1200px;top:1489px;text-align:center}
.card{top:1576px;width:298px;height:275px;background:var(--white);border-radius:12px;box-shadow:0 4px 20px rgba(10,80,140,.06);text-align:center;overflow:hidden}
.card.c1{left:112px}.card.c2{left:451px;background:linear-gradient(150deg,#1f9fe6,var(--blue-deep))}.card.c3{left:790px}
.card svg.icon{position:absolute;left:124px;top:30px}
.card h3{position:absolute;left:0;width:100%;top:104px;font-family:var(--serif);font-weight:400;font-size:23px;color:var(--ink)}
.card p{position:absolute;left:20px;width:258px;top:141px;font-size:14px;line-height:25.6px;color:var(--muted)}
.card.c2 h3,.card.c2 p{color:var(--white)}
.card .tab{position:absolute;left:111px;top:238px;width:76px;height:76px;border-radius:50%;background:var(--blue)}
.card.c2 .tab{background:var(--white)}
.card .tab svg{position:absolute;left:30px;top:14px}
.arrow{top:1701px}

/* contact */
.contact-title{left:111px;top:2013px}
.contact-lead{left:111px;top:2070px;width:420px;font-size:15px;line-height:26px}
.info{left:108px;display:flex;gap:14px;font-family:var(--serif);font-size:21px;line-height:34px;color:var(--ink)}
.info .dot{flex:0 0 40px;height:40px;border-radius:50%;background:var(--blue);display:flex;align-items:center;justify-content:center;margin-top:-2px}
.field{background:var(--field);box-shadow:0 2px 14px rgba(0,0,0,.05);font-family:var(--serif);font-size:17px;color:#333;padding:18px 28px}
.btn-submit{left:588px;top:2399px;width:130px;height:54px;font-size:20px}

/* footer */
.footer{left:0;top:2532px;width:1200px;height:470px;background:var(--footer)}
.foot-brand{left:0;width:1200px;top:2620px;text-align:center;font-family:var(--serif);font-weight:500;font-size:56px;color:var(--white);line-height:1}
.foot-nav{left:0;width:1200px;top:2763px;display:flex;justify-content:center;gap:58px;font-family:var(--serif);font-size:25px;color:var(--white);padding-left:12px}
.copy{left:0;width:1200px;top:2833px;text-align:center;font-family:var(--serif);font-size:20px;color:var(--white)}
.social{top:2901px;width:32px;height:32px;border-radius:50%;background:var(--white)}
</style>
</head>
<body>
<div class="page">

  <header>
    <div class="abs hero" role="img" aria-label="Dental clinic treatment room with blue tint"></div>
    <div class="abs brand">Harrowfield<small>Dentistry</small></div>
    <nav class="abs nav"><span>Home</span><span>About</span><span>Services</span><span>Contact Us</span></nav>
    <div class="abs btn-quote">Get A Quote</div>
    <h1 class="abs hero-title">Your Smile, Our Passion</h1>
    <p class="abs hero-sub">Modern, compassionate dental care in a comfortable setting.</p>
    <div class="abs btn-appt">Schedule an Appointment</div>
  </header>

  <section>
    <div class="abs about-bg"></div>
    <svg class="abs about-cut" width="1200" height="744" viewBox="0 0 1200 744"><polygon points="530,160 1200,160 1200,744 367,744" fill="#ffffff"/></svg>
    <div class="abs hero-photo" role="img" aria-label="Smiling patient during a dental check-up"></div>
    <div class="abs photo room" role="img" aria-label="Modern dental treatment chair"></div>
    <div class="abs photo smile" role="img" aria-label="Smiling woman with bright teeth"></div>
    <div class="abs photo consult" role="img" aria-label="Dentist consulting with a patient"></div>
    <h2 class="abs h2 about-title">About <b>Harrowfield Dentistry</b></h2>
    <div class="abs about-copy">
      <p>Lorem ipsum dolor sit amet, consectetur adipiscing elit, sed do eiusmod tempor incididunt ut labore et dolore magna aliqua. Ut enim ad minim veniam, quis nostrud exercitation ullamco laboris nisi ut aliquip ex ea commodo consequat.</p>
      <p>Duis aute irure dolor in reprehenderit in voluptate velit esse cillum dolore eu fugiat nulla pariatur. Excepteur sint occaecat cupidatat minim veniam, quis nostrud exercitation ullamco laboris nisi ut roideserunt mollit anim id est laborum.</p>
    </div>
    <div class="abs btn-blue btn-read">Read More</div>
  </section>

  <section>
    <div class="abs services-bg"></div>
    <h2 class="abs h2 services-title">Our <b>Services</b></h2>

    <svg class="abs arrow" style="left:42px" width="26" height="26" viewBox="0 0 26 26"><circle cx="13" cy="13" r="11.5" fill="none" stroke="#1c1c1c" stroke-width="1.6"/><path d="M18 13H8M12 9l-4 4 4 4" fill="none" stroke="#1c1c1c" stroke-width="1.6"/></svg>
    <svg class="abs arrow" style="left:1133px" width="26" height="26" viewBox="0 0 26 26"><circle cx="13" cy="13" r="11.5" fill="none" stroke="#1c1c1c" stroke-width="1.6"/><path d="M8 13h10M14 9l4 4-4 4" fill="none" stroke="#1c1c1c" stroke-width="1.6"/></svg>

    <article class="abs card c1">
      <svg class="icon" width="50" height="52" viewBox="0 0 50 52" fill="none" stroke="#222" stroke-width="2"><rect x="6" y="8" width="18" height="40" rx="2"/><rect x="9" y="2" width="12" height="6"/><rect x="24" y="28" width="22" height="20" rx="3"/><line x1="24" y1="35" x2="46" y2="35"/><path d="M15 20c-3 4-3 7 0 8 3-1 3-4 0-8z"/></svg>
      <h3>Cosmetic Dentistry</h3>
      <p>Duis aute irure dolor in reprehenderit in voluptate velit esse cillum dolore eu fugiat nulla pariatur.</p>
      <div class="tab"><svg width="16" height="10" viewBox="0 0 16 10"><path d="M2 8l6-6 6 6" fill="none" stroke="#fff" stroke-width="2.4"/></svg></div>
    </article>

    <article class="abs card c2">
      <svg class="icon" width="50" height="52" viewBox="0 0 50 52"><path d="M8 14c-4 4-2 14 8 24s20 12 24 8l-6-8-6 3c-4-2-8-6-10-10l3-6z" fill="#fff"/><circle cx="36" cy="14" r="11" fill="none" stroke="#fff" stroke-width="2.5"/><path d="M36 8v12M30 14h12" stroke="#fff" stroke-width="3"/></svg>
      <h3>Emergency Services</h3>
      <p>Duis aute irure dolor in reprehenderit in voluptate velit esse cillum dolore eu fugiat nulla pariatur.</p>
      <div class="tab"><svg width="16" height="10" viewBox="0 0 16 10"><path d="M2 8l6-6 6 6" fill="none" stroke="#0a90d8" stroke-width="2.4"/></svg></div>
    </article>

    <article class="abs card c3">
      <svg class="icon" width="50" height="60" viewBox="0 0 50 60" fill="none" stroke="#222" stroke-width="2"><rect x="10" y="2" width="34" height="6" rx="2"/><path d="M16 2V0M22 2V0M28 2V0"/><path d="M12 16c-6 0-8 8-6 16 2 6 4 10 5 20 1 6 6 6 7 0l3-12c1-3 5-3 6 0l3 12c1 6 6 6 7 0 1-10 3-14 5-20 2-8 0-16-6-16-5 0-8 3-12 3s-7-3-12-3z"/></svg>
      <h3>Dental Hygiene</h3>
      <p>Duis aute irure dolor in reprehenderit in voluptate velit esse cillum dolore eu fugiat nulla pariatur.</p>
      <div class="tab"><svg width="16" height="10" viewBox="0 0 16 10"><path d="M2 8l6-6 6 6" fill="none" stroke="#fff" stroke-width="2.4"/></svg></div>
    </article>
  </section>

  <section>
    <h2 class="abs h2 contact-title">Get in <b>Touch with us</b></h2>
    <p class="abs contact-lead">Lorem ipsum dolor sit aming elit, sed do eiusmod tempor incidiore et dolore magna aliqua.</p>

    <div class="abs info" style="top:2142px">
      <span class="dot"><svg width="16" height="22" viewBox="0 0 16 22"><path d="M8 1a7 7 0 0 0-7 7c0 5 7 13 7 13s7-8 7-13a7 7 0 0 0-7-7z" fill="#fff"/><circle cx="8" cy="8" r="2.6" fill="#0a90d8"/></svg></span>
      <span>Harrowfield Dentistry.<br>United States</span>
    </div>
    <div class="abs info" style="top:2230px">
      <span class="dot"><svg width="20" height="20" viewBox="0 0 20 20"><path d="M4 2c-3 3-1 8 4 13s10 6 12 3l-4-4-3 2c-2-1-4-3-5-5l2-3z" fill="#fff"/></svg></span>
      <span>+1 555 014 2287</span>
    </div>
    <div class="abs info" style="top:2293px">
      <span class="dot"><svg width="20" height="14" viewBox="0 0 20 14"><rect x="0" y="0" width="20" height="14" rx="2" fill="#fff"/><path d="M1 1l9 7 9-7" fill="none" stroke="#0a90d8" stroke-width="1.6"/></svg></span>
      <span>info@harrowfielddentistry.com</span>
    </div>
    <div class="abs info" style="top:2357px">
      <span class="dot"><svg width="20" height="20" viewBox="0 0 20 20"><circle cx="10" cy="10" r="8" fill="none" stroke="#fff" stroke-width="2"/><path d="M10 5v5h4" fill="none" stroke="#fff" stroke-width="2"/></svg></span>
      <span>Mon-Fri: 09.am to 07.pm<br>Saturday: 09.am to 5.00pm<br>Sunday: Closed</span>
    </div>

    <div class="abs field" style="left:588px;top:2025px;width:236px;height:58px">First Name</div>
    <div class="abs field" style="left:836px;top:2025px;width:252px;height:58px">Last Name</div>
    <div class="abs field" style="left:588px;top:2095px;width:236px;height:58px">Email</div>
    <div class="abs field" style="left:836px;top:2095px;width:252px;height:58px">Phone Number</div>
    <div class="abs field" style="left:588px;top:2167px;width:500px;height:205px">Message</div>
    <div class="abs btn-blue btn-submit">Submit</div>
  </section>

  <footer>
    <div class="abs footer"></div>
    <div class="abs foot-brand">Harrowfield Dentistry</div>
    <nav class="abs foot-nav"><span>Home</span><span>About</span><span>Services</span><span>Contact Us</span></nav>
    <p class="abs copy">Copyrights@20525.Harrowfield.All Rights Reserved</p>
    <span class="abs social" style="left:498px"></span>
    <span class="abs social" style="left:556px"></span>
    <span class="abs social" style="left:613px"></span>
    <span class="abs social" style="left:671px"></span>
  </footer>

</div>
</body>
</html>
```